Property Services Company Needs a Brochure Design

Looking for a new brochure design for an existing property services company.

We provide a range of property services from, market research, real estate brokerage, valuation and appraisal, property development and other real estate consulting services.

We would like a fresh modern brochure design with good graphics and features. Our colours are white, blue and orange.

The design should communicate, attention to detail, superior service delivery and distinction in results.
Updates

I would like the brochure to be roughly about 20 pages.

Containing the following,

1) An introduction
2) Contents Page
2) What we do
3) Our Services
4) Agency & Brokerage
5) Real Estate Consulting
6) Market Research
7) Appraisal & Valuation
8) Project Management
9) Property Development

I would also like icons to represent items 4,5,6,7,8 & 9, they should be represented vertically on each of the pages from the contents page and highlighted individually on the pages that they represent.. i.e. on appraisal & valuation page, all six icons will be arranged vertically and the appraisal and valuations icon will be highlighted.

I will also like to have images that depict the services on the various pages.

I have some pages I think will flow which I will upload shortly.

Industry/Entity Type

Real Estate

Font styles to use
Serif

Colors
f78f20
0455a3

```html
<!DOCTYPE html>
<html lang="en">
<head>
<meta charset="utf-8">
<title>Caldwick – Brochure Spreads</title>
<link rel="stylesheet" href="https://fonts.googleapis.com/css2?family=Open+Sans:wght@300;400;600;700&display=swap">
<style>
  :root{
    --orange:#f78f20;
    --orange-text:#d9831f;
    --blue:#0455a3;
    --blue-deep:#163a78;
    --ink:#2b2b2b;
    --paper:#ffffff;
    --paper-edge:#c9c9c9;
    --stage:#2e2e2e;
  }
  *{margin:0;padding:0;box-sizing:border-box}
  html,body{width:1200px;height:900px;overflow:hidden}
  body{background:var(--stage);font-family:"Open Sans",Arial,sans-serif;color:var(--ink);position:relative}

  .spread{position:absolute;overflow:hidden;box-shadow:0 6px 18px rgba(0,0,0,.55)}
  .line{display:block;white-space:nowrap}

  /* Spread 1 */
  .spread--intro{left:97px;top:78px;width:1020px;height:360px;
    background:radial-gradient(ellipse 70% 90% at 55% 45%,var(--paper) 35%,var(--paper-edge) 100%)}
  .intro__rule{position:absolute;left:26px;top:0;width:6px;height:100%;background:var(--orange)}
  .section-label{position:absolute;top:17px;font-size:10px;font-weight:700;color:#111;letter-spacing:.2px}
  .section-label--left{left:55px}
  .section-label--right{right:22px}
  .intro__body{position:absolute;left:51px;top:45px;font-size:10.2px;line-height:11.6px;color:#333}
  .intro__body p{margin-bottom:11.6px}
  .services{position:absolute;left:0;top:0;width:100%;height:100%}
  .service{position:absolute;display:flex;align-items:center;font-weight:700;font-size:17px}
  .service svg{flex:none;width:44px}
  .service--left{left:527px;gap:13px;color:var(--blue)}
  .service--right{right:24px;gap:18px;color:var(--orange-text)}
  .intro__band{position:absolute;left:511px;bottom:0;width:509px;height:36px;border-top:6px solid var(--orange);background:var(--blue-deep)}

  /* Spread 2 */
  .spread--services{left:107px;top:477px;width:1010px;height:356px;
    background:linear-gradient(90deg,#d8d8d8 0%,var(--paper) 25%,#e9e9e9 50%,var(--paper) 75%,#cfcfcf 100%)}
  .spread__art{position:absolute;left:0;top:0}
  .page-title{position:absolute;top:16px;color:#fff;font-weight:300;font-size:17px;letter-spacing:.2px}
  .page-title--agency{left:263px}
  .page-title--consulting{left:636px}
  .page-copy{position:absolute;font-size:10px;color:#333}
  .page-copy--agency{left:50px;top:151px;line-height:19px}
  .page-copy--consulting{right:12px;top:152px;text-align:right;line-height:17px;font-size:9.8px}
</style>
</head>
<body>

<section class="spread spread--intro" aria-label="What we do and our services">
  <div class="intro__rule"></div>
  <h2 class="section-label section-label--left">WHAT WE DO</h2>
  <h2 class="section-label section-label--right">OUR SERVICES</h2>

  <div class="intro__body">
    <p>
      <span class="line">Caldwick is a leading property services company, incorporated in 1984, providing bespoke</span>
      <span class="line">solutions in advisory, brokerage and turnkey solutions to owners, occupiers and property</span>
      <span class="line">investors. Over the years we have expanded our services with a foundation based on core</span>
      <span class="line">strengths, unrivalled local expertise, network and knowledge combined with strategic</span>
      <span class="line">partnership. As well as providing property solutions we also develop commercial and</span>
      <span class="line">residential units.</span>
    </p>
    <p>
      <span class="line">Our growth has been based on maintaining relationships with our extensive client base,</span>
      <span class="line">ranging from financial institutions, government agencies, airlines and servicing companies,</span>
      <span class="line">manufacturing companies, multinationals and local corporations, to private developers and</span>
      <span class="line">investors. Our clients depend on our ability to draw on years of experience in the local</span>
      <span class="line">market, our professionals know their communities and the property market inside and out,</span>
      <span class="line">and provide knowledgeable, creative solutions to all their real estate needs.</span>
    </p>
    <p>
      <span class="line">The combination of our integrated services allows us to provide a superior end to end solu-</span>
      <span class="line">tion to our clients, customized to their own requirements.&nbsp; Market research is a core compo-</span>
      <span class="line">nent to our business model, allowing us to make informed decisions based based on</span>
      <span class="line">research findings.&nbsp; Our brokerage team also benefits from this information, allowing our</span>
      <span class="line">associates to advise clients on how best to maximise return on their investment on the sale</span>
      <span class="line">or buy side within a short timeline.</span>
    </p>
    <p>
      <span class="line">We pay great attention to detail in consideration of our client requirements, delivering</span>
      <span class="line">mandates with distinction.</span>
    </p>
  </div>

  <div class="services">
    <div class="service service--left" style="top:54px">
      <svg height="52" viewBox="0 0 42 52" aria-hidden="true">
        <g fill="var(--orange)"><rect x="2" y="32" width="8" height="18"/><rect x="12" y="26" width="8" height="24"/><rect x="22" y="30" width="8" height="20"/><rect x="32" y="20" width="8" height="30"/></g>
        <polyline points="2,28 14,16 24,22 38,6" fill="none" stroke="var(--orange)" stroke-width="3"/>
        <polygon points="32,4 41,2 39,11" fill="var(--orange)"/>
      </svg>
      <span>Agency &amp; Brokerage</span>
    </div>
    <div class="service service--right" style="top:101px">
      <span>Appraisal &amp; Valuation</span>
      <svg height="42" viewBox="0 0 44 42" aria-hidden="true">
        <g fill="none" stroke="var(--blue)" stroke-width="2"><line x1="22" y1="3" x2="22" y2="38"/><line x1="5" y1="9" x2="39" y2="9"/><path d="M5 9 L1 24 M5 9 L9 24 M39 9 L35 24 M39 9 L43 24"/></g>
        <g fill="var(--blue)"><path d="M0 24 H10 A5 5 0 0 1 0 24Z"/><path d="M34 24 H44 A5 5 0 0 1 34 24Z"/><rect x="14" y="37" width="16" height="4"/></g>
      </svg>
    </div>
    <div class="service service--left" style="top:144px">
      <svg height="44" viewBox="0 0 48 44" aria-hidden="true">
        <circle cx="18" cy="18" r="16" fill="var(--orange)"/>
        <circle cx="18" cy="18" r="11" fill="#fff"/>
        <path d="M12 21 L18 15 L24 21 V25 H12Z" fill="var(--orange)"/>
        <line x1="30" y1="30" x2="45" y2="42" stroke="var(--orange)" stroke-width="5" stroke-linecap="round"/>
      </svg>
      <span>Real Estate Consulting</span>
    </div>
    <div class="service service--right" style="top:187px">
      <span>Project Management</span>
      <svg height="42" viewBox="0 0 42 42" aria-hidden="true">
        <rect width="42" height="42" rx="7" fill="var(--blue)"/>
        <path d="M11 20 A10 10 0 0 1 29 14" fill="none" stroke="#fff" stroke-width="3"/>
        <polygon points="26,9 33,15 25,17" fill="#fff"/>
        <path d="M31 22 A10 10 0 0 1 13 28" fill="none" stroke="#fff" stroke-width="3"/>
        <polygon points="16,33 9,27 17,25" fill="#fff"/>
      </svg>
    </div>
    <div class="service service--left" style="top:229px">
      <svg height="44" viewBox="0 0 42 44" role="img" aria-label="Market research team icon">
        <rect width="42" height="44" rx="4" fill="var(--orange)"/>
      </svg>
      <span>Market Research</span>
    </div>
    <div class="service service--right" style="top:276px">
      <span>Property Development</span>
      <svg height="36" viewBox="0 0 48 36" aria-hidden="true">
        <g fill="var(--blue)"><rect x="0" y="22" width="9" height="14" rx="2"/><rect x="13" y="14" width="9" height="22" rx="2"/><rect x="26" y="18" width="9" height="18" rx="2"/><rect x="39" y="0" width="9" height="36" rx="2"/></g>
      </svg>
    </div>
  </div>

  <div class="intro__band" role="img" aria-label="Blue honeycomb texture band"></div>
</section>

<section class="spread spread--services" aria-label="Agency and brokerage, real estate consulting">
  <svg class="spread__art" width="1010" height="356" viewBox="0 0 1010 356">
    <rect x="0" y="0" width="28" height="356" fill="var(--blue-deep)" role="img" aria-label="Blue honeycomb texture strip"/>
    <rect x="28" y="0" width="478" height="52" fill="var(--orange)"/>
    <polygon points="543,0 1010,0 1010,52 598,52" fill="var(--orange)"/>
    <polygon points="506,0 543,0 618,71 506,187" fill="var(--blue-deep)" role="img" aria-label="Blue honeycomb texture"/>
    <polygon points="618,71 923,356 343,356" fill="var(--blue-deep)" role="img" aria-label="Blue honeycomb texture"/>
    <defs>
      <linearGradient id="office-tone" x1="0" y1="0" x2="1" y2="1">
        <stop offset="0" stop-color="#e6e6e6"/><stop offset=".55" stop-color="#a9a9a9"/><stop offset="1" stop-color="#5b5b5b"/>
      </linearGradient>
      <clipPath id="office-clip"><polygon points="618,71 923,356 343,356"/></clipPath>
    </defs>
    <rect x="506" y="60" width="279" height="296" fill="url(#office-tone)" clip-path="url(#office-clip)" role="img" aria-label="Photo of a modern office with glass desk and chair"/>
    <line x1="543" y1="0" x2="923" y2="356" stroke="var(--orange)" stroke-width="6"/>
    <line x1="618" y1="71" x2="343" y2="356" stroke="var(--orange)" stroke-width="6"/>

    <rect x="41" y="0" width="102" height="134" fill="var(--orange)"/>
    <g fill="#fff"><rect x="54" y="82" width="14" height="28"/><rect x="72" y="72" width="14" height="38"/><rect x="90" y="64" width="14" height="46"/><rect x="108" y="54" width="14" height="56"/></g>
    <polyline points="52,66 74,46 90,54 122,22" fill="none" stroke="#fff" stroke-width="5"/>
    <polygon points="114,18 130,14 126,30" fill="#fff"/>

    <rect x="901" y="0" width="101" height="134" fill="var(--orange)"/>
    <circle cx="935" cy="48" r="20" fill="none" stroke="#e8e8e8" stroke-width="6"/>
    <path d="M925 52 L935 42 L945 52 V58 H925Z" fill="#e8e8e8"/>
    <line x1="950" y1="63" x2="990" y2="92" stroke="#e8e8e8" stroke-width="8" stroke-linecap="round"/>
  </svg>

  <h2 class="page-title page-title--agency">AGENCY &amp; BROKERAGE</h2>
  <h2 class="page-title page-title--consulting">REAL ESTATE CONSULTING</h2>

  <p class="page-copy page-copy--agency">
    <span class="line">The brokerage team, covers both landlords and tenants across the residential and</span>
    <span class="line">commercial markets. With a large database of industry specific individuals and corporate</span>
    <span class="line">twinned with a large database of inventory, we are able to very quickly understand</span>
    <span class="line">the needs of our clients and find the perfect fit. We enjoy long standing</span>
    <span class="line">relationships with many of our clients and landlords, and are always happy to</span>
    <span class="line">meet with new clients to advise on how best to maximize their rental</span>
    <span class="line">return or budget.</span>
  </p>

  <p class="page-copy page-copy--consulting">
    <span class="line">We provide a broad range of consulting services, we</span>
    <span class="line">understand that out client needs may vary and our</span>
    <span class="line">experienced team are at hand to provide tailored</span>
    <span class="line">solutions to their needs. Our professional</span>
    <span class="line">services include corporate planning,</span>
    <span class="line">feasibility studies, market studies, due</span>
    <span class="line">diligence, property tax, litigation,</span>
    <span class="line">asset review and framework for</span>
    <span class="line">foreign direct investment.</span>
  </p>
</section>

</body>
</html>
```